Flyer-Design für Shop für nachhaltige Haustierprodukte
LOMERU
Tolle Umsetzung nach den Vorgaben. Änderungen super und schnell umgesetzt. Gerne wieder!
Zielgruppe
LOMERU ist ein Online-Marktplatz für nachhaltige Haustierprodukte. Meine Zielgruppe sind Frauen zwischen 30 und 60 Jahren mit Haustieren (Hund, Katze, Pferd)
Aufgabenstellung
Das Design soll an der Webseite angepasst sein. Es ist wichtig, dass das Thema Nachhaltigkeit kommuniziert wird und welche Vorteile LOMERU hat (Markenvielvalt, kleine Manufakturen, Handmade etc.)

```html
<!DOCTYPE html>
<html lang="de">
<head>
<meta charset="utf-8">
<title>LOMERU – Flyer</title>
<link href="https://fonts.googleapis.com/css2?family=Montserrat:wght@400;500;700&display=swap" rel="stylesheet">
<style>
  :root {
    --orange: #ee7531;
    --ink: #141414;
    --grey: #4d4d4d;
    --paper: #ffffff;
    --horse: #a65a28;
    --horse-dark: #4a2a12;
    --cats: #6e6f72;
    --cats-red: #7a3a3e;
  }
  * { margin: 0; padding: 0; box-sizing: border-box; }
  html, body { width: 1200px; height: 2400px; overflow: hidden; background: var(--paper); }
  body { font-family: "Montserrat", Arial, sans-serif; position: relative; }

  .mission {
    position: absolute; left: 121px; top: 120px; width: 980px;
    font-size: 44px; font-weight: 500; line-height: 56.5px; color: var(--ink);
  }

  .features { position: absolute; left: 121px; top: 524px; width: 1000px; list-style: none; }
  .feature { position: relative; height: 199px; }
  .feature-icon { position: absolute; left: 0; top: 0; width: 141px; height: 141px; }
  .feature-text { position: absolute; left: 198px; top: 0; }
  .feature-title { font-size: 44px; font-weight: 700; color: var(--orange); line-height: 52px; letter-spacing: 0.3px; }
  .feature-desc { font-size: 30.5px; font-weight: 400; color: var(--grey); line-height: 44px; margin-top: 2px; letter-spacing: 0.4px; }

  .photo { position: absolute; top: 1568px; height: 624px; }
  .photo-horse { left: 0; width: 445px; background: linear-gradient(100deg, var(--horse-dark) 0%, var(--horse) 45%, #d08a3c 100%); }
  .photo-cats { left: 446px; width: 754px; background: linear-gradient(180deg, var(--cats-red) 0%, #5a5358 28%, var(--cats) 60%, #7d8388 100%); }

  .footer-band { position: absolute; left: 0; top: 2192px; width: 1200px; height: 208px; background: var(--orange); }
  .web-address {
    position: absolute; left: 121px; top: 2253px;
    font-size: 60px; font-weight: 700; color: var(--paper); letter-spacing: 0.5px;
  }
  .pet-badges { position: absolute; left: 741px; top: 2241px; width: 340px; height: 96px; }
</style>
</head>
<body>

<p class="mission">Unsere Mission ist es, mit einer ehrlichen Online-Plattform fair und ökologisch hergestellte Haustierprodukte sichtbar zu machen. Für ein nachhaltiges Leben mit Haustier und einen reduzierten ökologi-<br>schen Fußabdruck.</p>

<ul class="features">
  <li class="feature">
    <svg class="feature-icon" viewBox="0 0 141 141" aria-hidden="true">
      <circle cx="70.5" cy="70.5" r="67" fill="none" stroke="var(--orange)" stroke-width="6"/>
      <path d="M30 100 C 45 70, 70 55, 95 50 C 75 62, 60 75, 50 92 C 75 100, 108 80, 113 32 C 80 34, 45 45, 40 82 Z" fill="var(--orange)"/>
    </svg>
    <div class="feature-text">
      <h2 class="feature-title">Fair &amp; ökologisch</h2>
      <p class="feature-desc">Geringe Umweltbelastung bei der<br>Produktion und faire Bezahlung</p>
    </div>
  </li>
  <li class="feature">
    <svg class="feature-icon" viewBox="0 0 141 141" aria-hidden="true">
      <circle cx="70.5" cy="70.5" r="67" fill="none" stroke="var(--orange)" stroke-width="6"/>
      <path d="M36 38 H105 L115 60 Q115 70 106 70 Q97 70 97 62 Q97 70 88 70 Q79 70 79 62 Q79 70 70 70 Q61 70 61 62 Q61 70 52 70 Q43 70 43 62 Q43 70 34 70 Q25 70 26 60 Z" fill="var(--orange)"/>
      <path d="M32 75 H110 V112 H82 V90 H60 V112 H32 Z" fill="var(--orange)"/>
    </svg>
    <div class="feature-text">
      <h2 class="feature-title">Kleine Manufakturen</h2>
      <p class="feature-desc">Viele Produkte aus kleineren<br>Manufakturen, hergestellt mit Herzblut</p>
    </div>
  </li>
  <li class="feature">
    <svg class="feature-icon" viewBox="0 0 141 141" aria-hidden="true">
      <circle cx="70.5" cy="70.5" r="67" fill="none" stroke="var(--orange)" stroke-width="6"/>
      <path d="M52 40 Q52 34 57 34 Q62 34 62 40 V65 H64 V32 Q64 26 69 26 Q74 26 74 32 V65 H76 V35 Q76 29 81 29 Q86 29 86 35 V67 H88 V45 Q88 40 92 40 Q97 40 97 45 V90 Q97 112 75 112 H66 Q56 112 50 102 L38 82 Q35 76 40 73 Q45 71 49 76 L52 81 Z" fill="var(--orange)"/>
    </svg>
    <div class="feature-text">
      <h2 class="feature-title">Schadstofffrei</h2>
      <p class="feature-desc">Die Produkte enthalten keine schädliche<br>Chemie oder Schadstoffe</p>
    </div>
  </li>
  <li class="feature">
    <svg class="feature-icon" viewBox="0 0 141 141" aria-hidden="true">
      <circle cx="70.5" cy="70.5" r="67" fill="none" stroke="var(--orange)" stroke-width="6"/>
      <path d="M20 58 L45 42 L70 52 L45 68 Z M70 52 L96 42 L122 58 L96 68 Z" fill="var(--orange)"/>
      <path d="M36 70 L68 80 V112 L36 102 Z M74 80 L106 70 V102 L74 112 Z" fill="var(--orange)"/>
    </svg>
    <div class="feature-text">
      <h2 class="feature-title">Nachhaltig verpackt</h2>
      <p class="feature-desc">Nachhaltig Verpackt vom Packaging<br>bis hin zum Versandkarton</p>
    </div>
  </li>
  <li class="feature">
    <svg class="feature-icon" viewBox="0 0 141 141" aria-hidden="true">
      <circle cx="70.5" cy="70.5" r="67" fill="none" stroke="var(--orange)" stroke-width="6"/>
      <path d="M102 44 A36 36 0 1 0 102 98" fill="none" stroke="var(--orange)" stroke-width="15"/>
      <rect x="28" y="56" width="50" height="10" fill="var(--orange)"/>
      <rect x="28" y="76" width="50" height="10" fill="var(--orange)"/>
    </svg>
    <div class="feature-text">
      <h2 class="feature-title">Faire Preise</h2>
      <p class="feature-desc">Hochwertige Produkte mit<br>langer Lebensdauer zu fairen Preisen</p>
    </div>
  </li>
</ul>

<div class="photo photo-horse" role="img" aria-label="Foto: Kopf eines braunen Pferdes mit weißer Blesse im warmen Abendlicht"></div>
<div class="photo photo-cats" role="img" aria-label="Foto: zwei Katzen fressen gemeinsam aus einer weißen Schale vor einer roten Holzwand"></div>

<div class="footer-band"></div>
<p class="web-address">www.lomeru.de</p>
<svg class="pet-badges" viewBox="0 0 340 96" role="img" aria-label="Symbole für Hund, Katze und Pferd">
  <circle cx="49" cy="48" r="45" fill="none" stroke="var(--paper)" stroke-width="4"/>
  <circle cx="172" cy="48" r="45" fill="none" stroke="var(--paper)" stroke-width="4"/>
  <circle cx="293" cy="48" r="45" fill="none" stroke="var(--paper)" stroke-width="4"/>
</svg>

</body>
</html>
```